One page informative flyer for Florist

We are looking for a simple one page flyer. We are a florist who sell flowers, and commemorative t-shirts at graduation ceremonies, and need a flyer that can be given out to students so that they will know what is available on site. Further, we want the flyer to be editable (ie. a word template, or some other program), so that we can change the schools name, and change small bits of the copy easily.

What we are really looking for is a simple template, but we need 4 iterations of the flyer. With each of our two logos, I will need a flyer for t-shirts, and a flyer for flowers. Making 4 total. Please see breakdown below as explanation:

1, Tasselgate Flowers logo - flyer for flowers
2. Tasselgate Flowers logo - flyer for shirts
3. Mortarboard Bloom Co logo - flyer for flowers
4. Mortarboard Bloom Co logo - flyer for shirts

Please see logos for Tasselgate Flowers and Mortarboard Bloom Co attached, as well as a picture of flowers and of the shirts. Feel free to use those images or stock images.

Here is the copy:

Flowers - A variety floral arrangements will be available for purchase at our stand, located conveniently at the graduation ceremony. You can browse our selection & pre-order ahead of time at: www.mortarboardbloomco.example/index,php/test

T-Shirts - Commerative T-Shirts displaying all of the students names will be available for purchase at our stand, located conveniently at the graduation ceremony. You can pre-order ahead of time to guarantee your choice of size at: www.mortarboardbloomco.example/index.php/test

```html
<!DOCTYPE html>
<html lang="en">
<head>
<meta charset="utf-8">
<title>Mortarboard Bloom Co – Graduation T-Shirts Flyer</title>
<link href="https://fonts.googleapis.com/css2?family=Arimo:wght@400;700&family=Oswald:wght@500&display=swap" rel="stylesheet">
<style>
  :root {
    --paper: #eef3d2;
    --teal-dark: #22555f;
    --teal-text: #1f5766;
    --brand-green: #7b9b3e;
    --url-red: #c8303a;
    --frame-grey: #e2e2e2;
    --frame-grey-light: #f4f4f4;
  }
  html, body {
    margin: 0;
    padding: 0;
    overflow: hidden;
  }
  .flyer {
    position: relative;
    width: 851px;
    height: 1200px;
    background: var(--paper);
    font-family: "Arimo", Arial, sans-serif;
    overflow: hidden;
  }
  .school-tab {
    position: absolute;
    left: 0;
    top: 0;
    width: 263px;
    height: 378px;
    background: var(--teal-dark);
  }
  .school-tab__label {
    position: absolute;
    left: 62px;
    top: 170px;
    margin: 0;
    color: #ffffff;
    font-weight: 700;
    font-size: 27px;
    letter-spacing: 0.5px;
  }
  .header-rule {
    position: absolute;
    left: 263px;
    top: 368px;
    width: 588px;
    height: 10px;
    background: var(--teal-dark);
  }
  .brand-name {
    position: absolute;
    right: 45px;
    top: 78px;
    margin: 0;
    text-align: right;
    font-family: "Oswald", "Arial Narrow", sans-serif;
    font-weight: 500;
    font-size: 84px;
    line-height: 98px;
    color: var(--brand-green);
  }
  .product-photo {
    position: absolute;
    left: 211px;
    top: 422px;
    width: 426px;
    height: 352px;
    border: 2px solid var(--teal-dark);
    border-radius: 20px;
    background: radial-gradient(ellipse at center, var(--frame-grey-light) 0%, var(--frame-grey) 100%);
  }
  .offer-copy {
    position: absolute;
    left: 78px;
    top: 818px;
    width: 700px;
    margin: 0;
    color: var(--teal-text);
    font-size: 26.5px;
    line-height: 38.5px;
  }
  .offer-url {
    position: absolute;
    left: 78px;
    top: 1056px;
    margin: 0;
    color: var(--url-red);
    font-weight: 700;
    font-size: 27px;
  }
</style>
</head>
<body>
  <main class="flyer">
    <div class="school-tab">
      <p class="school-tab__label">SCHOOL</p>
    </div>
    <div class="header-rule"></div>

    <h1 class="brand-name">Mortarboard<br>Bloom Co</h1>

    <div class="product-photo" role="img" aria-label="Two white commemorative graduation T-shirts: front with school name and crest, back listing the graduating class names"></div>

    <p class="offer-copy">T-Shirts - Commerative T-Shirts displaying all of the students names will be available for purchase at our stand, located conveniently at the graduation cere&shy;mony. You can pre-order ahead of time to guaran&shy;tee your choice of size at:</p>

    <p class="offer-url">www.mortarboardbloomco.example</p>
  </main>
</body>
</html>
```